Wine Bottle Label Logo Design

My fiancé and I are getting married in September and we made homemade wine which will be given to the guests as a wedding favor. We need label/logo for our wine bottles. We were looking for something rustic yet modern and simple. We had an idea for beige and cranberry colored wine stained, weathered, imperfect heart. Things that will need to be incorporated into the label design are as follows:
Our last name and also the name of the wine: Carudi
The year: 2012
Where is says Alcohol Content on a wine bottle normally write: Alcohol: Deceiving% by vol.
Type of wine: Red Wine
Incorporate our wedding date: Foot Stomped and Bottled for Marla and Ned's Wedding Day 9/28/13

```html
<!DOCTYPE html>
<html lang="en">
<head>
<meta charset="utf-8">
<title>Carudi Red Wine Label</title>
<link href="https://fonts.googleapis.com/css2?family=Libre+Baskerville:ital,wght@0,700;1,700&family=Source+Sans+3:wght@400;600;700&display=swap" rel="stylesheet">
<style>
  :root {
    --backdrop: #e9e7e4;
    --cranberry: #c4213f;
    --cranberry-deep: #8e1425;
    --ribbon-red: #6e0f1a;
    --cream: #f3e7c4;
    --gold: #b8914a;
    --gold-light: #d9bb7c;
    --ink: #2a1a14;
    --blush: #f3c3cb;
  }
  html, body {
    margin: 0;
    padding: 0;
    overflow: hidden;
  }
  .canvas {
    width: 1200px;
    height: 1000px;
    background: var(--backdrop);
    display: flex;
    align-items: center;
    justify-content: center;
    overflow: hidden;
  }
  .wine-label {
    width: 576px;
    height: 893px;
    display: block;
  }
  .label-body { fill: var(--cranberry); stroke: var(--gold); stroke-width: 3; }
  .label-inner-line { fill: none; stroke: var(--gold-light); stroke-width: 0.8; }
  .diamond-panel { fill: var(--cream); stroke: var(--gold); stroke-width: 3; }
  .diamond-line { fill: none; stroke: var(--cranberry); stroke-width: 0.7; }
  .ribbon-tail { fill: var(--ribbon-red); }
  .banner-fold { fill: #8a6a33; }
  .banner { fill: var(--gold); stroke: var(--gold-light); stroke-width: 0.6; }
  .alcohol-note {
    font-family: "Source Sans 3", sans-serif;
    font-weight: 700;
    font-size: 5.6px;
    fill: var(--ink);
  }
  .wine-type {
    font-family: "Libre Baskerville", serif;
    font-style: italic;
    font-weight: 700;
    font-size: 11.5px;
    fill: var(--cranberry);
  }
  .wine-name {
    font-family: "Libre Baskerville", serif;
    font-weight: 700;
    font-size: 31px;
    fill: var(--cranberry);
  }
  .dedication {
    font-family: "Source Sans 3", sans-serif;
    font-weight: 400;
    font-size: 8.6px;
    fill: var(--ink);
  }
  .edition {
    font-family: "Source Sans 3", sans-serif;
    font-weight: 600;
    font-size: 7.4px;
    fill: var(--cranberry-deep);
  }
  .wedding-date {
    font-family: "Source Sans 3", sans-serif;
    font-weight: 400;
    font-size: 8.6px;
    fill: var(--blush);
  }
</style>
</head>
<body>
<main class="canvas">
  <svg class="wine-label" viewBox="0 0 240 372" xmlns="http://www.w3.org/2000/svg">
    <defs>
      <path id="date-arc" d="M64,250 Q120,285 178,250"/>
    </defs>

    <!-- label shape -->
    <path class="label-body" d="M8,62 L8,36 Q28,36 30,16 L92,16 Q120,4 148,16 L210,16 Q212,36 232,36 L232,62 L226,70 L226,196 L232,204 L232,224 Q212,224 206,236 Q196,280 120,284 Q44,280 34,236 Q28,224 8,224 L8,204 L14,196 L14,70 Z"/>
    <path class="label-inner-line" d="M13,64 L13,40 Q32,40 34,21 L93,21 Q120,10 147,21 L206,21 Q208,40 227,40 L227,64 L221,72 L221,194 L227,202 L227,219 Q209,219 201,233 Q192,275 120,279 Q48,275 39,233 Q31,219 13,219 L13,202 L19,194 L19,72 Z"/>

    <!-- cream diamond panel -->
    <path class="diamond-panel" d="M120,30 L232,142 L120,254 L8,142 Z"/>
    <path class="diamond-line" d="M120,37 L225,142 L120,247 L15,142 Z"/>

    <!-- hanging ribbon -->
    <path class="ribbon-tail" d="M86,222 L150,222 L150,370 L118,340 L86,370 Z"/>

    <!-- edition banner -->
    <path class="banner-fold" d="M20,206 L44,206 L44,226 L20,226 L28,216 Z"/>
    <path class="banner-fold" d="M220,206 L196,206 L196,226 L220,226 L212,216 Z"/>
    <path class="banner" d="M36,202 Q120,190 204,202 L204,222 Q120,210 36,222 Z"/>

    <!-- text -->
    <text class="alcohol-note" x="120" y="72" text-anchor="middle">Deceiving% by vol.</text>
    <text class="wine-type" x="120" y="96" text-anchor="middle">Red Wine</text>
    <text class="wine-name" x="120" y="138" text-anchor="middle">Carudi</text>
    <text class="dedication" x="120" y="180" text-anchor="middle">Foot Stomped and Bottled</text>
    <text class="dedication" x="120" y="191" text-anchor="middle">for Marla and Ned's</text>
    <text class="edition" x="120" y="211" text-anchor="middle">2012 EDITION</text>
    <text class="wedding-date" text-anchor="middle">
      <textPath href="#date-arc" startOffset="50%">Wedding Day 9/28/13</textPath>
    </text>
  </svg>
</main>
</body>
</html>
```